Four in One (Flexible infographic for Content Management Industry)

See attachment.
A graphic depicting 4 products, where each can stand on its own and each can be combined with others, but where, if all are taken together, the best result is achieved (the "super product").
Intended use is web. See attached file as an example.
The most basic idea is as the attached diagram shows, where 4 rectangles are arranged in a quadrangle, with a middle rectangle in the center representing the combined 4 products. This concept is fine except it is a bit too obvious as it stands. We are looking for either a variation of this or another concept.
The audience is technical + professional + enterprise - NOT consumers. Hence the design should be conservative in nature.
We are aware of tools like as Canva or Pictogram where such graphics are available, but we are looking for something with a bit more imagination and flexibility.
This graphic should be targeted to web sites and be delivered with vector-based (SVG) graphics.

```html
<!DOCTYPE html>
<html lang="en">
<head>
<meta charset="utf-8">
<title>Super Product – Four in One</title>
<link rel="stylesheet" href="https://fonts.googleapis.com/css2?family=Montserrat:wght@600;700;800;900&display=swap">
<style>
  :root {
    --frame-grey: #9a9b9d;
    --page-bg: #ffffff;
    --ink-dark: #444446;
    --tab-accent: #b9cfdc;
    --text-light: #ffffff;
  }
  html, body {
    margin: 0;
    padding: 0;
    width: 1200px;
    height: 982px;
    overflow: hidden;
    background: var(--page-bg);
  }
  .infographic {
    display: block;
    width: 1200px;
    height: 982px;
    font-family: "Montserrat", Arial, sans-serif;
  }
  .outer-frame { fill: var(--page-bg); stroke: var(--frame-grey); stroke-width: 8; stroke-linejoin: miter; }
  .petal-line { fill: none; stroke: var(--text-light); stroke-width: 3.5; }
  .icon-tab { fill: var(--page-bg); }
  .tab-accent { fill: var(--tab-accent); }
  .center-pill { fill: var(--page-bg); }
  .center-title { fill: var(--ink-dark); font-size: 100px; font-weight: 900; letter-spacing: 1px; }
  .petal-title { fill: var(--text-light); font-size: 38px; font-weight: 700; letter-spacing: 0.5px; }
  .petal-title--small { font-size: 33px; }
  .title-rule { stroke: var(--text-light); stroke-width: 3; }
  .petal-body { fill: var(--text-light); font-size: 19.5px; font-weight: 700; }
  .petal-body--heavy { font-weight: 800; }
  .feature-list { fill: var(--text-light); font-size: 19.5px; font-weight: 700; letter-spacing: 0.4px; }
  .tick { fill: none; stroke: var(--text-light); stroke-width: 3.5; stroke-linecap: round; stroke-linejoin: round; }
  .icon-line { fill: none; stroke: #111; stroke-width: 5; stroke-linejoin: round; stroke-linecap: round; }
  .icon-solid { fill: #111; }
</style>
</head>
<body>
<svg class="infographic" viewBox="0 0 2120 1736" xmlns="http://www.w3.org/2000/svg" role="img" aria-label="Super Product: four combined solutions">
  <defs>
    <linearGradient id="grad-document" x1="0" y1="0" x2="1" y2="1">
      <stop offset="0" stop-color="#6f5aa8"/>
      <stop offset="1" stop-color="#443867"/>
    </linearGradient>
    <linearGradient id="grad-security" x1="0" y1="0" x2="1" y2="1">
      <stop offset="0" stop-color="#bb168e"/>
      <stop offset="1" stop-color="#8c1f70"/>
    </linearGradient>
    <linearGradient id="grad-erp" x1="0" y1="0" x2="1" y2="1">
      <stop offset="0" stop-color="#2fc5de"/>
      <stop offset="1" stop-color="#30606f"/>
    </linearGradient>
    <linearGradient id="grad-digital" x1="0" y1="0" x2="1" y2="1">
      <stop offset="0" stop-color="#117fa8"/>
      <stop offset="1" stop-color="#2a5490"/>
    </linearGradient>

    <g id="petal-shape">
      <path d="M388,195 H735 C900,195 1027,330 1027,500 V830 H650 C500,810 388,690 388,530 Z"/>
    </g>
    <g id="petal-details">
      <path class="petal-line" d="M415,258 V220 H735 C885,220 1000,345 1000,500 V775"/>
      <path class="petal-line" d="M415,402 V530 C415,680 520,790 668,805"/>
      <polygon class="tab-accent" points="328,402 388,402 388,437"/>
      <path class="icon-tab" d="M328,258 H565 A73,73 0 0 1 638,331 V402 H328 Z"/>
    </g>
    <path id="tick" class="tick" d="M0,7 L5,12 L14,1"/>
  </defs>

  <!-- Outer frame -->
  <path class="outer-frame" d="M345,150 H735 C900,150 1020,250 1063,400 C1105,250 1225,150 1385,150 H1780 V212 H1836 V445 L1780,478 V540 C1780,700 1690,810 1535,868 C1690,925 1780,1040 1780,1200 V1270 L1836,1305 V1535 H1780 V1585 H1385 C1225,1585 1105,1485 1063,1335 C1020,1485 900,1585 735,1585 H345 V1535 H287 V1305 L345,1270 V1200 C345,1040 435,925 595,868 C435,810 345,700 345,540 V478 L287,445 V212 H345 Z"/>

  <!-- Petals -->
  <g class="petal petal--document">
    <use href="#petal-shape" fill="url(#grad-document)"/>
    <use href="#petal-details"/>
  </g>
  <g class="petal petal--security" transform="translate(2126,0) scale(-1,1)">
    <use href="#petal-shape" fill="url(#grad-security)"/>
    <use href="#petal-details"/>
  </g>
  <g class="petal petal--erp" transform="translate(0,1736) scale(1,-1)">
    <use href="#petal-shape" fill="url(#grad-erp)"/>
    <use href="#petal-details"/>
  </g>
  <g class="petal petal--digital" transform="translate(2126,1736) scale(-1,-1)">
    <use href="#petal-shape" fill="url(#grad-digital)"/>
    <use href="#petal-details"/>
  </g>

  <!-- Center label -->
  <rect class="center-pill" x="650" y="775" width="826" height="173" rx="86"/>
  <text class="center-title" x="1058" y="898" text-anchor="middle">Super Product</text>

  <!-- Icons -->
  <g class="icon icon--document">
    <path class="icon-line" d="M503,281 H556 L570,295 V371 H503 Z"/>
    <path class="icon-line" d="M556,281 V295 H570"/>
    <path class="icon-line" d="M514,305 H558 M514,318 H558 M514,331 H558 M514,344 H558"/>
  </g>
  <g class="icon icon--shield">
    <path class="icon-line" d="M1586,279 L1627,294 V330 C1627,354 1610,370 1586,380 C1562,370 1545,354 1545,330 V294 Z" stroke-width="6"/>
    <circle class="icon-solid" cx="1586" cy="331" r="25"/>
    <path d="M1574,331 L1583,340 L1599,322" fill="none" stroke="#fff" stroke-width="6" stroke-linecap="round" stroke-linejoin="round"/>
  </g>
  <g class="icon icon--documents">
    <path class="icon-line" d="M502,1386 H578 V1472 H502 Z"/>
    <path class="icon-line" d="M492,1374 H567 V1460 H492 Z" fill="#fff"/>
    <path class="icon-line" d="M503,1392 H556 M503,1405 H556 M503,1418 H556 M503,1431 H556 M503,1444 H540"/>
  </g>
  <g class="icon icon--wifi">
    <path class="icon-line" d="M1530,1396 C1556,1370 1598,1370 1624,1396" stroke-width="10"/>
    <path class="icon-line" d="M1545,1413 C1564,1396 1590,1396 1609,1413" stroke-width="10"/>
    <path class="icon-line" d="M1560,1430 C1570,1422 1584,1422 1594,1430" stroke-width="9"/>
    <circle class="icon-solid" cx="1577" cy="1446" r="13"/>
  </g>

  <!-- Document Management -->
  <g class="panel-text panel-text--document">
    <text class="petal-title" x="710" y="463" text-anchor="middle">Document Management</text>
    <line class="title-rule" x1="475" y1="487" x2="960" y2="487"/>
    <text class="petal-body" text-anchor="end">
      <tspan x="975" y="532">Streamline document organization, access, and</tspan>
      <tspan x="975" y="556">collaboration with easier file storage and sharing,</tspan>
      <tspan x="975" y="581">leading to more efficient workflows .</tspan>
    </text>
    <use href="#tick" x="538" y="638"/><use href="#tick" x="538" y="662"/><use href="#tick" x="538" y="687"/><use href="#tick" x="538" y="711"/>
    <text class="feature-list">
      <tspan x="562" y="650">Centralized Document Control</tspan>
      <tspan x="562" y="674">Collaborative Workspace Integration</tspan>
      <tspan x="562" y="699">Automated Compliance Tracking</tspan>
      <tspan x="562" y="723">Check 4</tspan>
    </text>
  </g>

  <!-- Security and Compliance -->
  <g class="panel-text panel-text--security">
    <text class="petal-title" x="1158" y="463">Security and Compliance</text>
    <line class="title-rule" x1="1163" y1="487" x2="1667" y2="487"/>
    <text class="petal-body petal-body--heavy">
      <tspan x="1160" y="532">Benefit from tailored cloud solutions, secure data</tspan>
      <tspan x="1160" y="557">storage, and expert disaster recovery planning for</tspan>
      <tspan x="1160" y="581">reliable and scalable IT operations.</tspan>
    </text>
    <use href="#tick" x="1170" y="638"/><use href="#tick" x="1170" y="662"/><use href="#tick" x="1170" y="687"/><use href="#tick" x="1170" y="711"/>
    <text class="feature-list">
      <tspan x="1207" y="650">Custom Cloud Solutions</tspan>
      <tspan x="1207" y="674">Secure Data Storage</tspan>
      <tspan x="1207" y="699">Expert Disaster Recovery</tspan>
      <tspan x="1207" y="723">Check 4</tspan>
    </text>
  </g>

  <!-- Enterprise Resource Planning -->
  <g class="panel-text panel-text--erp">
    <text class="petal-title petal-title--small" x="495" y="1052">Enterprise Resource Planning</text>
    <line class="title-rule" x1="499" y1="1073" x2="970" y2="1073"/>
    <text class="petal-body" text-anchor="end">
      <tspan x="972" y="1117">Simplify management across finance, sales, and</tspan>
      <tspan x="972" y="1141">operations, enabling better decision-making</tspan>
      <tspan x="972" y="1166">and improved productivity.</tspan>
    </text>
    <use href="#tick" x="514" y="1224"/><use href="#tick" x="514" y="1249"/><use href="#tick" x="514" y="1273"/><use href="#tick" x="514" y="1298"/>
    <text class="feature-list">
      <tspan x="543" y="1236">Integrated Business Processes</tspan>
      <tspan x="543" y="1261">Enhanced Decision-Making</tspan>
      <tspan x="543" y="1285">Productivity Improvement</tspan>
      <tspan x="543" y="1310">Check 4</tspan>
    </text>
  </g>

  <!-- Digital Transformation -->
  <g class="panel-text panel-text--digital">
    <text class="petal-title" x="1158" y="1052">Digital Transformation</text>
    <line class="title-rule" x1="1163" y1="1073" x2="1635" y2="1073"/>
    <text class="petal-body">
      <tspan x="1160" y="1119">Turn scanned documents into easily searchable</tspan>
      <tspan x="1160" y="1143">digital archives, boosting efficiency and</tspan>
      <tspan x="1160" y="1168">accessibility.</tspan>
    </text>
    <use href="#tick" x="1170" y="1224"/><use href="#tick" x="1170" y="1249"/><use href="#tick" x="1170" y="1273"/><use href="#tick" x="1170" y="1298"/>
    <text class="feature-list">
      <tspan x="1207" y="1236">Instant searchable Archives with OCR</tspan>
      <tspan x="1207" y="1261">Automated Document Classification</tspan>
      <tspan x="1207" y="1285">VaultPoint and Cloud Blob Ready</tspan>
      <tspan x="1207" y="1310">Check 4</tspan>
    </text>
  </g>
</svg>
</body>
</html>
```